Crestline Staffing PEO - Web Build for Professional Employment Organization

We need a website built for our new PEO (professional employment organization). This company will offer third party Human Resource services to companies who are looking to outsource:<br/>Recruiting<br/>Administrative Onboarding<br/>New hire training, ongoing training and development<br/>Payroll/compensation processing/services<br/>Employee Relations<br/>Unemployment Claim Facilitation<br/>Benefits Plans and Administration<br/><br/>I have attached the logo below. Please use that as a reference and color match as best as possible. <br/><br/>Here are some of the competitor's websites:<br/>https://www.velmorahr.com/ <br/>https://www.trundelpay.com/<br/>https://www.trundelpay.com/<br/>https://www.qzn.com/<br/>https://www.bremwickhr.com/<br/>https://orvalepeo.com/contact-orvale/<br/><br/>

Target Market(s)

Startups and mid-sized businesses

Number of Pages Required

5+ page

Font styles to use
Sans Serif

Colors
0592cd

Requirements
Must have
• Features Pages
• SEO driven keyword rich content
• Strong focus on our ability to provide unemployment claim facilitation services as well as mandatory training/certification fulfillment
Nice to have
• I'd like to see one mockup with a Live Chat version if possible. In theory, the Live Chat messages would go directly to our front desk person.

```html
<!DOCTYPE html>
<html lang="en">
<head>
<meta charset="utf-8">
<title>Crestline Staffing PEO</title>
<link href="https://fonts.googleapis.com/css2?family=Mulish:wght@400;600;700;800&display=swap" rel="stylesheet">
<style>
:root{
  --brand:#1e88c9;
  --brand-deep:#1479bf;
  --navy:#131c33;
  --navy-2:#1b2540;
  --ink:#333a45;
  --muted:#6d7890;
  --card:#eaf2fb;
  --white:#ffffff;
}
*{box-sizing:border-box;margin:0;padding:0}
html,body{width:1200px;height:3686px;overflow:hidden}
body{font-family:"Mulish",sans-serif;color:var(--ink);background:var(--white);position:relative}
.abs{position:absolute}
a{text-decoration:none;color:inherit}

/* header */
.site-header{position:absolute;left:0;top:0;width:1200px;height:88px;background:var(--white)}
.brand{position:absolute;left:143px;top:22px;display:flex;align-items:center;gap:10px}
.brand-mark{width:18px;height:18px;background:var(--brand)}
.brand-name{font-weight:800;font-size:24px;color:var(--navy-2);letter-spacing:.5px}
.main-nav{position:absolute;right:145px;top:28px;display:flex;gap:34px;font-size:13px;text-transform:uppercase;color:#555}
.main-nav .active{color:var(--brand)}

/* hero */
.hero{position:absolute;left:0;top:88px;width:1200px;height:700px}
.hero-title{position:absolute;left:0;width:1200px;top:190px;text-align:center;color:#fff;font-weight:800;font-size:32px;line-height:40px;text-shadow:0 2px 6px rgba(0,0,0,.45)}
.hero-btn{position:absolute;left:528px;top:280px;width:144px;height:47px;background:var(--brand-deep);color:#fff;font-weight:700;font-size:16px;display:flex;align-items:center;justify-content:center}
.hero-arrow{position:absolute;top:239px;width:48px;height:48px;border-radius:50%;background:rgba(20,28,50,.8);display:flex;align-items:center;justify-content:center}

/* welcome */
.section-title{position:absolute;left:0;width:1200px;text-align:center;color:var(--brand);font-weight:600;font-size:40px;text-transform:uppercase}
.welcome-copy{position:absolute;left:143px;width:914px;top:903px;text-align:center;font-size:16px;line-height:29px;color:#444}

/* services */
.services{position:absolute;left:0;top:1094px;width:1200px;height:680px;background:radial-gradient(circle at 70% 40%,#1d2a4c,var(--navy) 70%)}
.services h2{position:absolute;left:143px;top:72px;font-size:40px;font-weight:600;color:var(--brand)}
.services-intro{position:absolute;left:143px;top:126px;width:420px;font-size:16px;line-height:26px;color:#aab3c5}
.service{position:absolute;width:420px;height:96px}
.service-icon{position:absolute;left:0;top:0;width:96px;height:96px;border-radius:50%;background:#fff;display:flex;align-items:center;justify-content:center}
.service-text{position:absolute;left:116px;top:16px;width:300px}
.service-text h3{font-size:18px;font-weight:600;color:#fff;line-height:22px}
.service-text p{margin-top:6px;font-size:11px;line-height:17px;color:#7f8aa3}

/* resources */
.carousel-arrow{position:absolute;top:2050px}
.resource-card{position:absolute;top:1905px;width:298px;height:330px;background:var(--card)}
.resource-photo{height:178px}
.resource-card h3{margin:22px 20px 0;font-size:16px;font-weight:600;line-height:21px;color:var(--brand)}
.resource-card p{margin:12px 20px 0;font-size:10px;line-height:17px;color:#444}
.resource-btn{position:absolute;left:20px;bottom:-15px;width:96px;height:31px;background:var(--brand-deep);color:#fff;font-size:12px;display:flex;align-items:center;justify-content:center}
.rule{position:absolute;left:0;top:2328px;width:1200px;height:1px;background:#cfd5dd}

/* certification */
.cert-art{position:absolute;left:143px;top:2488px;width:442px;height:236px;background:linear-gradient(135deg,#e6f3fb,#b9def2 55%,#3a7fd4)}
.cert-copy{position:absolute;left:143px;top:2753px;width:440px;font-size:16px;line-height:26px;color:#444}
.courses-head{position:absolute;left:627px;top:2490px;width:428px;padding-bottom:18px;border-bottom:1px solid #c9cdd3;font-size:23px;color:#222}
.course-list{position:absolute;left:627px;top:2562px;list-style:none}
.course-list li{height:46.5px;display:flex;align-items:center;gap:14px;font-size:21px;color:var(--brand)}

/* contact */
.contact{position:absolute;left:0;top:2936px;width:1200px;height:540px;background:radial-gradient(circle at 50% 40%,#1a8ad2,var(--brand-deep) 60%,#0f66a8)}
.contact h2{position:absolute;left:0;width:1200px;top:68px;text-align:center;color:#fff;font-weight:600;font-size:40px}
.field{position:absolute;background:#fff;font-size:12px;color:#555;padding:17px 15px}
.submit{position:absolute;left:552px;top:349px;width:96px;height:39px;background:var(--navy);color:#fff;font-size:13px;display:flex;align-items:center;justify-content:center}

/* partners & footer */
.site-footer{position:absolute;left:0;top:3475px;width:1200px;height:211px;background:var(--navy)}
.partners{position:absolute;left:143px;top:3405px;width:912px;height:127px;background:#fff;display:flex;align-items:center;justify-content:space-around;padding:0 10px}
.partners span{font-size:18px;font-weight:700;color:#222;display:flex;align-items:center;gap:6px}
.partners i{width:12px;height:12px;border-radius:50%;background:#222;display:inline-block}
.footer-nav{position:absolute;left:145px;top:3581px;font-size:12px;color:#8d97ad}
.footer-nav a{margin-right:8px}
.footer-nav b{font-weight:400;margin-right:8px}
.copyright{position:absolute;left:145px;top:3615px;font-size:12px;color:#8d97ad}
.social{position:absolute;left:680px;top:3596px;display:flex;gap:22px}
.social span{width:20px;height:20px;border-radius:50%;border:2px solid #7a86a0;display:block}
.live-chat{position:absolute;left:815px;top:3584px;width:240px;height:47px;border-radius:24px;background:var(--brand-deep);color:#fff;font-weight:700;font-size:16px;display:flex;align-items:center;justify-content:center;gap:12px}
</style>
</head>
<body>

<header class="site-header">
  <a class="brand" href="#"><span class="brand-mark"></span><span class="brand-name">CRESTLINE STAFFING PEO</span></a>
  <nav class="main-nav">
    <a class="active" href="#">Home</a><a href="#">About Us</a><a href="#">Services</a><a href="#">Reources</a><a href="#">Contact Us</a>
  </nav>
</header>

<section class="hero">
  <svg width="1200" height="700" viewBox="0 0 1200 700" class="abs" style="left:0;top:0">
    <defs>
      <linearGradient id="heroTone" x1="0" y1="0" x2="1" y2="1">
        <stop offset="0" stop-color="#5b5f63"/><stop offset=".45" stop-color="#a39a8e"/><stop offset="1" stop-color="#3f4651"/>
      </linearGradient>
    </defs>
    <polygon points="0,0 1200,0 1200,527 1030,598 343,684 0,527" fill="url(#heroTone)" role="img" aria-label="Photo of two businessmen shaking hands across an office desk"/>
    <polygon points="0,527 343,684 343,692" fill="#2a3552"/>
    <polygon points="343,684 1030,598 860,640 343,692" fill="#2a3552"/>
    <polygon points="860,640 1030,598 1010,597" fill="#1565a6"/>
    <polygon points="1010,597 1200,527 1030,598" fill="#1e88c9"/>
  </svg>
  <h1 class="hero-title">MAECENAS EGET TORTOR<br>ACCUMSAN QUAM</h1>
  <a class="hero-btn" href="#">READ MORE</a>
  <span class="hero-arrow" style="left:47px"><svg width="16" height="20"><path d="M12 2 4 10l8 8" stroke="#fff" stroke-width="3" fill="none"/></svg></span>
  <span class="hero-arrow" style="left:1103px"><svg width="16" height="20"><path d="M4 2l8 8-8 8" stroke="#fff" stroke-width="3" fill="none"/></svg></span>
</section>

<h2 class="section-title" style="top:845px">Welcome to PEO</h2>
<p class="welcome-copy">Phasellus consequat sagittis nisi suscipit feugiat. Cras eget leo sed nunc hendrerit ultricies nisl. Praesent iaculis faucibus urna sit amet lacinia. Maecenas consequat justo enim, ac mattis massa imperdiet quis. Fusce eget neque elit. Sed augue orci, elementum in magna congue, tincidunt vulputate erat. Aliquam consectetur orci molestie dictum molestie. Proin eget congue nulla, vel tempor diam.</p>

<section class="services">
  <h2>SERVICES</h2>
  <p class="services-intro">Fusce sollicitudin luctus volutpat. Proin placerat dapibus gravida. In tristique tristique nulla hendrerit. Maecenas vel tortor accumsan quam.</p>

  <div class="service" style="left:143px;top:229px">
    <span class="service-icon"><svg width="44" height="40" fill="none" stroke="#1e88c9" stroke-width="2"><circle cx="12" cy="12" r="6"/><circle cx="32" cy="12" r="6"/><path d="M2 38c0-10 20-10 20 0M22 38c0-10 20-10 20 0"/></svg></span>
    <div class="service-text"><h3>Recruiting</h3><p>Etiam vel massa elementum, bibendum tellus venenatis, feugiat massa. Curabitur venenatis lacinia ornare</p></div>
  </div>
  <div class="service" style="left:143px;top:358px">
    <span class="service-icon"><svg width="40" height="40" fill="none" stroke="#1e88c9" stroke-width="2"><circle cx="20" cy="13" r="8"/><path d="M4 38c0-14 32-14 32 0"/></svg></span>
    <div class="service-text"><h3>Administrative Onboarding</h3><p>Etiam vel massa elementum, bibendum tellus venenatis, feugiat massa. Curabitur venenatis lacinia ornare</p></div>
  </div>
  <div class="service" style="left:143px;top:494px">
    <span class="service-icon"><svg width="40" height="40" fill="none" stroke="#1e88c9" stroke-width="2"><rect x="4" y="4" width="32" height="22"/><path d="M10 20l7-7 5 4 8-9M12 26l-4 12M28 26l4 12"/></svg></span>
    <div class="service-text"><h3>New hire training, ongoing training and development</h3><p>Etiam vel massa elementum, bibendum tellus venenatis, feugiat massa. Curabitur venenatis lacinia ornare</p></div>
  </div>

  <div class="service" style="left:645px;top:93px">
    <span class="service-icon"><svg width="40" height="40" fill="none" stroke="#1e88c9" stroke-width="2"><rect x="6" y="3" width="22" height="34" rx="2"/><path d="M11 9h12M11 16h4M19 16h4M11 22h4M19 22h4"/><circle cx="30" cy="30" r="7"/></svg></span>
    <div class="service-text"><h3>Payroll/compensation processing/ services</h3><p>Etiam vel massa elementum, bibendum tellus venenatis, feugiat massa. Curabitur venenatis lacinia ornare</p></div>
  </div>
  <div class="service" style="left:645px;top:222px">
    <span class="service-icon"><svg width="40" height="40" fill="none" stroke="#1e88c9" stroke-width="2"><path d="M2 16l10-8 8 6 8-6 10 8M8 20l10 10 4-2 10-10"/></svg></span>
    <div class="service-text"><h3>Employee Relations</h3><p>Etiam vel massa elementum, bibendum tellus venenatis, feugiat massa. Curabitur venenatis lacinia ornare</p></div>
  </div>
  <div class="service" style="left:645px;top:358px">
    <span class="service-icon"><svg width="40" height="40" fill="none" stroke="#1e88c9" stroke-width="2"><circle cx="20" cy="10" r="6"/><path d="M6 38V22l8 8M34 38V22l-8 8M14 22h12"/></svg></span>
    <div class="service-text"><h3>Unemployment Claim Facilitation</h3><p>Etiam vel massa elementum, bibendum tellus venenatis, feugiat massa. Curabitur venenatis lacinia ornare</p></div>
  </div>
  <div class="service" style="left:645px;top:494px">
    <span class="service-icon"><svg width="40" height="40" fill="none" stroke="#1e88c9" stroke-width="2"><rect x="13" y="2" width="14" height="10"/><rect x="2" y="28" width="10" height="10"/><rect x="15" y="28" width="10" height="10"/><rect x="28" y="28" width="10" height="10"/><path d="M20 12v8M7 28v-8h26v8M20 20v8"/></svg></span>
    <div class="service-text"><h3>Benefits Plans and Administration</h3><p>Etiam vel massa elementum, bibendum tellus venenatis, feugiat massa. Curabitur venenatis lacinia ornare</p></div>
  </div>
</section>

<h2 class="section-title" style="top:1842px">Resources</h2>
<svg class="carousel-arrow" style="left:55px" width="16" height="30"><path d="M14 2 3 15l11 13" stroke="#555" stroke-width="3" fill="none"/></svg>
<svg class="carousel-arrow" style="left:1126px" width="16" height="30"><path d="M2 2l11 13L2 28" stroke="#555" stroke-width="3" fill="none"/></svg>

<article class="resource-card" style="left:143px">
  <div class="resource-photo" role="img" aria-label="Photo of colleagues meeting around a conference table" style="background:linear-gradient(135deg,#8d9aa6,#4b5866)"></div>
  <h3>Cras sollicitudin cursus dui eu placerat massa.</h3>
  <p>Quisque aliquet ex nec est vestibulum pulvinar. Pellentesque convallis molestie enim amet efficitur. Etiam id imperdiet lectus.</p>
  <a class="resource-btn" href="#">READ MORE</a>
</article>
<article class="resource-card" style="left:451px">
  <div class="resource-photo" role="img" aria-label="Photo of two women talking at a desk" style="background:linear-gradient(135deg,#b9b3ad,#4d4a4a)"></div>
  <h3>Maecenas consequat justo enim mattis massa</h3>
  <p>Quisque aliquet ex nec est vestibulum pulvinar. Pellentesque convallis molestie enim amet efficitur. Etiam id imperdiet lectus.</p>
  <a class="resource-btn" href="#">READ MORE</a>
</article>
<article class="resource-card" style="left:757px">
  <div class="resource-photo" role="img" aria-label="Photo of a man and woman working on a laptop" style="background:linear-gradient(135deg,#c8c6c0,#5b554f)"></div>
  <h3>Aenean facilisis tincidunt lectus id dictum nisi luctus</h3>
  <p>Quisque aliquet ex nec est vestibulum pulvinar. Pellentesque convallis molestie enim amet efficitur. Etiam id imperdiet lectus.</p>
  <a class="resource-btn" href="#">READ MORE</a>
</article>

<div class="rule"></div>

<h2 class="section-title" style="top:2400px">Certification Courses</h2>
<div class="cert-art" role="img" aria-label="Illustration of two people presenting growth charts on a large screen"></div>
<p class="cert-copy">Phasellus blandit quam a ipsum gravida dapibus. Cras sed augue tortor. Suspendisse elit ligula, iaculis dignissim justo eu, vestibulum venenatis.</p>
<h3 class="courses-head">Our Courses</h3>
<ul class="course-list">
  <li><svg width="19" height="19"><circle cx="9.5" cy="9.5" r="9.5" fill="#1e88c9"/><path d="M8 5l4 4.5L8 14" stroke="#fff" stroke-width="2.2" fill="none"/></svg>Donec a nisl vel ante tristique</li>
  <li><svg width="19" height="19"><circle cx="9.5" cy="9.5" r="9.5" fill="#1e88c9"/><path d="M8 5l4 4.5L8 14" stroke="#fff" stroke-width="2.2" fill="none"/></svg>Nullam accumsan purus vel tempus</li>
  <li><svg width="19" height="19"><circle cx="9.5" cy="9.5" r="9.5" fill="#1e88c9"/><path d="M8 5l4 4.5L8 14" stroke="#fff" stroke-width="2.2" fill="none"/></svg>Suspendisse elit ligula, iaculis dignissim</li>
  <li><svg width="19" height="19"><circle cx="9.5" cy="9.5" r="9.5" fill="#1e88c9"/><path d="M8 5l4 4.5L8 14" stroke="#fff" stroke-width="2.2" fill="none"/></svg>Aliquam malesuada eros sit</li>
  <li><svg width="19" height="19"><circle cx="9.5" cy="9.5" r="9.5" fill="#1e88c9"/><path d="M8 5l4 4.5L8 14" stroke="#fff" stroke-width="2.2" fill="none"/></svg>Fusce porta arcu mi aliquet dictum nulla</li>
  <li><svg width="19" height="19"><circle cx="9.5" cy="9.5" r="9.5" fill="#1e88c9"/><path d="M8 5l4 4.5L8 14" stroke="#fff" stroke-width="2.2" fill="none"/></svg>Phasellus congue dapibus sapien</li>
</ul>

<section class="contact">
  <h2>CONTACT US</h2>
  <div class="field" style="left:224px;top:134px;width:240px;height:42px;padding-top:13px">Name</div>
  <div class="field" style="left:480px;top:134px;width:240px;height:42px;padding-top:13px">Email</div>
  <div class="field" style="left:736px;top:134px;width:240px;height:42px;padding-top:13px">Phone</div>
  <div class="field" style="left:224px;top:194px;width:752px;height:132px;padding-top:14px">Message</div>
  <a class="submit" href="#">SUBMIT</a>
</section>

<footer class="site-footer"></footer>
<div class="partners">
  <span><i></i>Tidewell</span><span>Barrowfin</span><span>Kelpmark</span><span>Saltmere</span><span>Larkspun</span><span>Fennick</span><span>Quillbeck</span>
</div>
<nav class="footer-nav"><a href="#">Home</a><b>|</b><a href="#">About Us</a><b>|</b><a href="#">Services</a><b>|</b><a href="#">Reources</a><b>|</b><a href="#">Contact Us</a></nav>
<p class="copyright">Copyright © 2020 Crestline Staffing PEO. All rights reserved.</p>
<div class="social"><span aria-label="Social link"></span><span aria-label="Social link"></span><span aria-label="Social link"></span></div>
<a class="live-chat" href="#"><svg width="24" height="20"><path d="M2 3h14v9H7l-4 3v-3H2z" fill="#fff"/><path d="M18 6h4v9h-1v3l-4-3h-6v-2h7z" fill="#fff"/></svg>LIVE CHAT WITH US</a>

</body>
</html>
```